Gift Card and Gift Card Holder Design

Hello I need a design for a gift card and the gift card holder. I am uploading two PDFs for examples of designs we used for other promotional flyers. I am also uploading some design templates - two gift card holder templates (each would require the same design) and one gift card template. Also attached are two images of another gift card design - simple front, back had areas for text. We will need these areas for text in the design. We will provide copy for those areas but we should be able to edit following the close of the design project with you.

Font styles to use
Sans Serif

Colors
ec1f27
0455a3

Requirements
Must have
• use this web site for color reference: https://quorvelfit.com/
• use this website for design inspiration for custom gift card holders: https://plintaroworks.com/customgiftcardholder.html
• option with $75 on front of card as value
• two more options without

```html
<!DOCTYPE html>
<html lang="en">
<head>
<meta charset="utf-8">
<title>QVF Window Blinds – $75 Gift Card</title>
<link href="https://fonts.googleapis.com/css2?family=Archivo+Black&family=Bebas+Neue&display=swap" rel="stylesheet">
<style>
  :root{
    --brand-red:#a10b0b;
    --brand-red-deep:#7a0a0a;
    --brand-blue:#0a1fd0;
    --brand-blue-deep:#0a2a9a;
    --wood-light:#c9cfd2;
    --wood-mid:#a7aeb1;
    --wood-dark:#8a8f90;
    --slot:#1c1e1e;
    --white:#ffffff;
  }
  html,body{margin:0;padding:0;overflow:hidden;background:#ffffff;}
  .gift-card{
    position:relative;width:1200px;height:754px;overflow:hidden;
    font-family:"Archivo Black",Arial,sans-serif;
  }
  .wood-backdrop{
    position:absolute;inset:0;
    background:linear-gradient(180deg,var(--wood-light) 0%,#bfc6c8 45%,var(--wood-mid) 75%,var(--wood-dark) 100%);
  }
  .brand-block{
    position:absolute;left:44px;top:43px;width:318px;height:248px;
    display:flex;align-items:flex-end;justify-content:flex-start;gap:14px;
  }
  .brand-square{width:44px;height:44px;background:var(--brand-red);margin-bottom:12px;}
  .brand-name{font-size:100px;color:var(--brand-red);line-height:1;}
  .brand-line{
    position:absolute;left:46px;top:298px;margin:0;white-space:nowrap;
    font-size:29px;color:var(--white);letter-spacing:1px;
    text-shadow:2px 3px 3px rgba(0,0,0,.45);
  }
  .headline{
    position:absolute;left:385px;top:120px;margin:0;white-space:nowrap;
    font-size:72px;line-height:1;letter-spacing:.5px;
    text-shadow:2px 3px 3px rgba(0,0,0,.35);
  }
  .headline .initials{color:var(--brand-red);}
  .headline .trade{color:var(--brand-blue);}
  .tagline{
    position:absolute;left:388px;top:190px;margin:0;white-space:nowrap;
    font-size:15px;color:var(--white);letter-spacing:.2px;
    text-shadow:1px 2px 2px rgba(0,0,0,.6);
  }
  .value-line{
    position:absolute;left:0;top:448px;margin:0;width:100%;height:200px;
    font-family:"Bebas Neue",Impact,sans-serif;font-weight:400;
    font-size:200px;line-height:1;letter-spacing:0;
    text-shadow:3px 4px 4px rgba(0,0,0,.55);
  }
  .value-line span{position:absolute;top:0;white-space:nowrap;transform-origin:left top;}
  .value-line .amount{left:170px;color:var(--brand-red-deep);transform:scaleX(.87);}
  .value-line .label{left:427px;color:var(--brand-blue-deep);}
  .slot{position:absolute;background:var(--slot);}
  .slot-top{left:502px;top:67px;width:200px;height:44px;border-radius:22px;}
  .slot-side{left:1090px;top:278px;width:43px;height:198px;border-radius:22px;}
  .slot-hole{left:44px;top:625px;width:88px;height:88px;border-radius:50%;}
</style>
</head>
<body>
  <main class="gift-card">
    <div class="wood-backdrop" role="img" aria-label="Weathered grey wood planks with a faint room interior behind a window"></div>

    <div class="brand-block">
      <span class="brand-square"></span>
      <span class="brand-name">QVF</span>
    </div>
    <p class="brand-line">Installed Solutions</p>

    <div class="slot slot-top"></div>

    <h1 class="headline"><span class="initials">QVF</span> <span class="trade">Window Blinds</span></h1>
    <p class="tagline">The preferred installer of window treatments to the builder, homeowner, and remodelers.</p>

    <div class="slot slot-side"></div>

    <h2 class="value-line"><span class="amount">$75</span><span class="label">GIFT CARD</span></h2>

    <div class="slot slot-hole"></div>
  </main>
</body>
</html>
```